KVOR Individual and Corporate Development Business Card Design

KVOR needs a business card design that is aligned with it's values and targetted markets. Coherent Lattice of Adaptive Reasoning Method's self diagnosis model and tools, which can be used for personal improvement and team/business performance enhancement, is based on the learnings of over 20 years of medical practitioning. KVOR supercharges personal effectiveness and awareness to also increase team and business performance.

The targetted markets are high performance individuals and teams who aspire seek to enhance their capabilities and achieve their absolute best potential.

Look and feel for the business card design we are looking for is high technology, premium, fresh, new and medical.

Target Market(s)

Industry/Entity Type

Business Consultant

Contact Information for Business Card

Logo, Full Name, Title, Phone number, Email, company name, Address,

Font styles to use
Sans Serif

Requirements
Must have
• Tag line: Sharpening Focus for Teams Who Reach for Their Best
• Please use same colours as the logo.

```html
<!DOCTYPE html>
<html lang="en">
<head>
<meta charset="utf-8">
<title>KVOR Business Card</title>
<link href="https://fonts.googleapis.com/css2?family=Roboto:ital,wght@0,400;0,500;0,700;1,400&family=Roboto+Condensed:wght@700&display=swap" rel="stylesheet">
<style>
  :root {
    --backdrop: #2b2b2b;
    --brand-teal: #03a9c1;
    --card-white: #f3f3f3;
    --ink-grey: #555a5e;
    --stripe-grey: #4d5257;
    --white: #ffffff;
  }
  * { margin: 0; padding: 0; box-sizing: border-box; }
  html, body { width: 1200px; height: 960px; overflow: hidden; }
  body {
    background: var(--backdrop);
    font-family: "Roboto", Arial, sans-serif;
    position: relative;
  }
  .card {
    position: absolute;
    width: 600px;
    height: 343px;
    box-shadow: 0 3px 8px rgba(0,0,0,.45);
  }
  .card--front { left: 314px; top: 113px; background: var(--card-white); }
  .card--back { left: 311px; top: 472px; background: var(--brand-teal); }

  .brand {
    position: absolute;
    display: flex;
    align-items: center;
    gap: 12px;
    font-weight: 700;
    letter-spacing: 2px;
    line-height: 1;
  }
  .brand__mark { width: 14px; height: 14px; }
  .card--front .brand { left: 56px; top: 58px; font-size: 56px; color: var(--brand-teal); }
  .card--front .brand__mark { background: var(--brand-teal); }
  .card--back .brand { left: 0; right: 0; top: 140px; justify-content: center; font-size: 64px; color: var(--white); }
  .card--back .brand__mark { background: var(--white); }

  .company {
    position: absolute;
    left: 32px;
    top: 178px;
    width: 230px;
    font-size: 14px;
    font-weight: 500;
    line-height: 20px;
    color: var(--ink-grey);
  }
  .address {
    position: absolute;
    left: 33px;
    top: 220px;
    font-size: 15px;
    line-height: 19px;
    color: var(--ink-grey);
  }
  .contacts {
    position: absolute;
    left: 33px;
    top: 263px;
    list-style: none;
    font-size: 14.5px;
    line-height: 19.5px;
    color: var(--ink-grey);
  }
  .contacts li { display: flex; align-items: center; gap: 7px; }
  .contacts svg { width: 14px; height: 14px; fill: var(--brand-teal); }

  .name-band { position: absolute; right: 0; top: 225px; width: 224px; height: 56px; }
  .name-band svg { position: absolute; inset: 0; }
  .name-band__text {
    position: absolute;
    right: 33px;
    top: 6px;
    text-align: center;
    color: var(--white);
    font-family: "Roboto Condensed", Arial, sans-serif;
    font-weight: 700;
  }
  .name-band__name { font-size: 21px; line-height: 24px; }
  .name-band__title { font-size: 15px; line-height: 20px; }

  .tagline {
    position: absolute;
    left: 0; right: 0;
    top: 292px;
    text-align: center;
    font-size: 14px;
    font-style: italic;
    color: var(--white);
  }
</style>
</head>
<body>
  <section class="card card--front">
    <div class="brand"><span class="brand__mark"></span>KVOR</div>
    <p class="company">Coherent Lattice of Adaptive Reasoning Method</p>
    <p class="address">214 Larkspur Row<br>Fairbanks, Alaska 99701</p>
    <ul class="contacts">
      <li><svg viewBox="0 0 16 16"><path d="M3.6 1.5l2.3 2.6-1.4 1.8c.9 2 2.6 3.7 4.6 4.6l1.8-1.4 2.6 2.3-1.4 2.2C7 13.3 2.7 9 2 3z"/></svg>907 555 0148</li>
      <li><svg viewBox="0 0 16 16"><path d="M1 3.5h14v9H1zM2.5 5v.4L8 9l5.5-3.6V5L8 8.4z"/></svg>hello@kvor-method.com</li>
      <li><svg viewBox="0 0 16 16"><circle cx="8" cy="8" r="7"/></svg>www.kvor-method.com</li>
    </ul>
    <div class="name-band">
      <svg viewBox="0 0 224 56" aria-hidden="true">
        <polygon points="38,0 52,0 14,56 0,56" fill="var(--stripe-grey)"/>
        <polygon points="54,0 224,0 224,56 16,56" fill="var(--brand-teal)"/>
      </svg>
      <div class="name-band__text">
        <div class="name-band__name">MAREN HOLT</div>
        <div class="name-band__title">CEO/FOUNDER</div>
      </div>
    </div>
  </section>

  <section class="card card--back">
    <div class="brand"><span class="brand__mark"></span>KVOR</div>
    <p class="tagline">Sharpening Focus for Teams Who Reach for Their Best</p>
  </section>
</body>
</html>
```